Business Card - high end, modern health care

Hey designers!

We need a double sided business card for the boutique, cutting edge physical therapy rehabilitation centre in Sydney's Northern Beaches.

With the most qualified physios in the area The Harbourview Motion Clinic does what other physiotherapy practices do not, we take our time with our patients giving them longer appointments, better physios and therefor faster results!

We guarantee that the service people receive at THMC will be unparalleled.

Hence we need a business card to reflect our modern, boutique, high end service. The final design needs to reflect that we are in a class of our own yet with the feel of beachside retreat.

Below I have attached our logo in both blue on white and white on blue. The exact colour is;
and the font that we have used in our logo is Tex Gyre Aventador.

I like the idea of the blue as the main colour as it is more eye catching and our signage onto the main road will be in this blue and in the interest of consistency across marketing the blue needs to be a part of the design. However I would appreciate a few designs onto a wooden background as this is a visual theme within the fitout of the practice.

The design needs to be of standard size (91x55mm).

Target Market(s)

We target people who have an end outcome in mind and those who have had poor experiences with other providers and ensure that everyone gets the care that they deserve with a premium service that is tailored to the individuals circumstances. As a premium service, the target market is highly educated, business and tech savvy with the additional target market of elderly people who have self funded their retirement and see value in paying for the best ongoing rehabilitation to maintain independence.

Industry/Entity Type

Physical Therapy

Contact Information for Business Card

Name, designation( Titled Musculoskeletal Physiotherapist... there will also be those in the company that have multiple designations ie 5 or 6 words long), phone number, email, facebook, instagram, address

Font styles to use
Sans Serif

Colors

Designer to choose colors to be used in the design.

Requirements
Must have
• Front - The logo as large as possible, blue or wooden theme, and all of the important details.
• Back - A blank space/lines on which to write appointment times (no "Appointment, date, time" etc.)
Nice to have
• facebook url
• logos for facebook and instagram
• Mini logos for the phone and email?

```html
<!DOCTYPE html>
<html lang="en">
<head>
<meta charset="utf-8">
<title>The Harbourview Motion Clinic – Business Card</title>
<link rel="stylesheet" href="https://fonts.googleapis.com/css2?family=Montserrat:wght@500;700&family=Roboto:wght@400;500&display=swap">
<style>
  :root {
    --brand-blue: #1f63b8;
    --card-white: #fbfbfb;
    --ink: #4a4a4a;
    --rule: #8a8a8a;
    --watermark: #e6ecf4;
    --stage: #e9e7e3;
  }
  * { box-sizing: border-box; margin: 0; padding: 0; }
  html, body { width: 1200px; height: 911px; overflow: hidden; }
  body {
    background: var(--stage);
    font-family: "Roboto", Arial, sans-serif;
    position: relative;
  }
  .card {
    position: absolute;
    width: 540px;
    height: 326px;
    background: var(--card-white);
    border-radius: 18px;
    box-shadow: 0 6px 18px rgba(0,0,0,0.12);
    overflow: hidden;
  }
  .card--front { left: 40px; top: 292px; }
  .card--back { left: 620px; top: 292px; }

  /* Front */
  .brand {
    position: absolute;
    left: 34px;
    top: 150px;
    display: flex;
    align-items: center;
    gap: 10px;
  }
  .brand__dot {
    width: 38px; height: 38px;
    border-radius: 50%;
    background: var(--brand-blue);
    flex: none;
  }
  .brand__name {
    font-family: "Montserrat", Arial, sans-serif;
    color: var(--brand-blue);
    font-weight: 700;
    line-height: 1.05;
  }
  .brand__line1 { font-size: 23px; letter-spacing: 0.2px; display: block; }
  .brand__line2 { font-size: 12.5px; letter-spacing: 4px; display: block; margin-top: 3px; }

  .contact {
    position: absolute;
    left: 86px;
    top: 208px;
    color: var(--ink);
    font-size: 11.5px;
    line-height: 16px;
    font-style: normal;
    display: flex;
    gap: 18px;
  }
  .contact__address { width: 130px; }
  .contact__list { list-style: none; }
  .contact__row { display: flex; align-items: center; gap: 7px; }
  .contact__icon { width: 11px; height: 11px; flex: none; }

  .staff-band {
    position: absolute;
    right: 0;
    top: 62px;
    width: 250px;
    height: 72px;
    background: var(--brand-blue);
    border-radius: 36px 0 0 36px;
    display: flex;
    align-items: center;
    padding-left: 12px;
    gap: 16px;
  }
  .staff-band__dot {
    width: 50px; height: 50px;
    border-radius: 50%;
    background: var(--card-white);
    flex: none;
  }
  .staff-band__name {
    color: #fff;
    font-weight: 500;
    font-size: 19px;
    letter-spacing: 0.3px;
    line-height: 1.1;
  }
  .staff-band__role {
    color: #fff;
    font-size: 12px;
    letter-spacing: 0.3px;
    display: block;
    margin-top: 2px;
    font-weight: 400;
  }

  /* Back */
  .back-watermark {
    position: absolute;
    left: 150px;
    top: 60px;
    width: 240px;
    height: 210px;
    border-radius: 50%;
    background: var(--watermark);
  }
  .appointment-lines {
    position: absolute;
    left: 30px;
    right: 30px;
    top: 26px;
    list-style: none;
  }
  .appointment-lines__row {
    height: 34px;
    border-bottom: 1px solid var(--rule);
  }
</style>
</head>
<body>

<section class="card card--front" aria-label="Business card front">
  <div class="brand">
    <span class="brand__dot"></span>
    <h1 class="brand__name">
      <span class="brand__line1">THE HARBOURVIEW</span>
      <span class="brand__line2">MOTION CLINIC</span>
    </h1>
  </div>

  <address class="contact">
    <p class="contact__address">42 Tidewater Parade<br>Collaroy, NSW 2097</p>
    <ul class="contact__list">
      <li class="contact__row">
        <svg class="contact__icon" viewBox="0 0 12 12"><path d="M3 1 L5 3.5 L4 5 Q5 7 7 8 L8.5 7 L11 9 L10 11 Q4 11 1 2 Z" fill="var(--brand-blue)"/></svg>
        02 9971 4408
      </li>
      <li class="contact__row">
        <svg class="contact__icon" viewBox="0 0 12 12"><rect x="1" y="2.5" width="10" height="7" rx="1" fill="var(--brand-blue)"/><path d="M1.5 3 L6 6.5 L10.5 3" stroke="#fff" stroke-width="1" fill="none"/></svg>
        daniel@harbourviewmotion.com
      </li>
      <li class="contact__row">
        <svg class="contact__icon" viewBox="0 0 12 12"><circle cx="6" cy="6" r="5" fill="var(--brand-blue)"/><path d="M1 6 H11 M6 1 Q3 6 6 11 Q9 6 6 1" stroke="#fff" stroke-width="0.8" fill="none"/></svg>
        www.harbourviewmotion.com
      </li>
      <li class="contact__row">
        <svg class="contact__icon" viewBox="0 0 12 12"><rect x="1" y="1" width="10" height="10" rx="1.5" fill="var(--brand-blue)"/></svg>
        /harbourviewmotion
      </li>
      <li class="contact__row">
        <svg class="contact__icon" viewBox="0 0 12 12"><circle cx="6" cy="6" r="5" fill="var(--brand-blue)"/></svg>
        @harbourviewclinic
      </li>
    </ul>
  </address>

  <div class="staff-band">
    <span class="staff-band__dot"></span>
    <p class="staff-band__name">DANIEL REYES<span class="staff-band__role">CEO/FOUNDER</span></p>
  </div>
</section>

<section class="card card--back" aria-label="Business card back">
  <div class="back-watermark"></div>
  <ol class="appointment-lines">
    <li class="appointment-lines__row"></li>
    <li class="appointment-lines__row"></li>
    <li class="appointment-lines__row"></li>
    <li class="appointment-lines__row"></li>
    <li class="appointment-lines__row"></li>
    <li class="appointment-lines__row"></li>
    <li class="appointment-lines__row"></li>
    <li class="appointment-lines__row"></li>
  </ol>
</section>

</body>
</html>
```